Bright Harbor, LLC Business Card Design

We need a product business card designed for a new company Bright Harbor, LLC. We make and resell waterless RV cleaner, polish and protectant. It cleans and protects in a simple spray and wipe step leaving the surface protected and conditioned to repel dust, dirt, water, smudges, bugs and fingerprints while preventing fogging. Safe on acrylic, plexiglas, lexan, plastic, rubber, painted surfaces, chrome, stainless, aluminum, vinyl, leather, glass.... This is an eco-friendly green product.

We want to play off the company name to tell the consumer that the product is easy to use and associate to the nostalgics 1950's in the USA... Thinking old travel trailer with hot rod truck pulling it as the graphic, maybe the husband cleaning the truck and the wife cleaning the trailer for a Bright Harbor surface.
Updates

Just posted our newly finished logo. Need to have "Cleaner and Protectant" added to the design as well. Thanks everyone that has submitted thus far, i am working to get comments on all.

If you need a different file format, please let me know. Thank you.

Most important info, is the logo, website and the words "Cleaner" or "Clean" along "Protectant" or "Protect" the remainder is of less importance. Highlight: www.brightharborwash.example Focus is on company brand for Brighter Harbor Cleaner product: However, need a section for the following contact info: Walt Ferris (xxx) xxx-xxxx email address Would like space for QR Code if possible.

Target Market(s)

Adults in the USA between ages of 35-75 that are actively involved in the Recreational Vehicle (RV), travel trailer, and hot rod lifestyle. We are targeting the RV marked of the high end travel, 5th wheel and bus RV market. Along with hot rods, automotive and motorcycle market.

Industry/Entity Type

Travel

Requirements
Must have
• Most important info, is the logo, website and the words "Cleaner" or "Clean" along "Protectant" or "Protect" the remainder is of less importance.

Highlight:
www.brightharborwash.example

Focus is on company brand for Brighter Harbor Cleaner product: However, need a section for the following contact info:

Walt Ferris
(xxx) xxx-xxxx
email address
Nice to have
• Would like a space for a QR Code.

```html
<!DOCTYPE html>
<html lang="en">
<head>
<meta charset="utf-8">
<title>Bright Harbor, LLC – Business Card</title>
<link rel="stylesheet" href="https://fonts.googleapis.com/css2?family=Exo+2:wght@400;500;600;800&display=swap">
<style>
  :root {
    --page-bg: #e6e4e1;
    --card-white: #ffffff;
    --card-shade: #e4e5e7;
    --ink: #1f1f26;
    --ink-soft: #3a3a42;
    --band-deep: #3b43a6;
    --band-mid: #2a6fcf;
    --band-light: #12aeea;
    --swoosh-grey: #a9abb0;
    --on-band: #ffffff;
    --qr-line: #9a9ca3;
  }
  * { margin: 0; padding: 0; box-sizing: border-box; }
  html, body {
    width: 1200px; height: 900px; overflow: hidden;
    background: var(--page-bg);
    font-family: "Exo 2", sans-serif;
    color: var(--ink);
  }
  .sheet {
    width: 1200px; height: 900px;
    display: flex; flex-direction: column; align-items: center; justify-content: center;
    gap: 60px;
  }
  .card {
    position: relative;
    width: 630px; height: 360px;
    background: radial-gradient(ellipse at 55% 45%, var(--card-white) 35%, var(--card-shade) 100%);
    box-shadow: 0 10px 24px rgba(0,0,0,0.18);
    overflow: hidden;
  }
  .card__wave { position: absolute; inset: 0; width: 100%; height: 100%; }
  .brand-name {
    font-weight: 800;
    letter-spacing: 0.5px;
    color: var(--ink);
    text-transform: uppercase;
    white-space: nowrap;
    line-height: 1;
  }
  .tagline {
    font-weight: 600;
    color: var(--band-mid);
    text-transform: uppercase;
    letter-spacing: 2px;
    white-space: nowrap;
  }
  .card--front .brand-block { position: absolute; left: 38px; top: 110px; }
  .card--front .brand-name { font-size: 38px; }
  .card--front .tagline { font-size: 14px; margin-top: 8px; letter-spacing: 2.4px; }
  .person {
    position: absolute; left: 40px; top: 282px;
    color: var(--on-band);
  }
  .person__name { font-size: 20px; font-weight: 500; letter-spacing: 1.5px; text-transform: uppercase; }
  .person__role { font-size: 13px; margin-top: 2px; }
  .contact {
    position: absolute; left: 400px; top: 48px;
    font-size: 13px; color: var(--ink-soft); line-height: 1.35;
  }
  .contact__address { font-size: 14px; margin-bottom: 18px; letter-spacing: 0.3px; }
  .contact__list { list-style: none; }
  .contact__list li { display: flex; align-items: center; gap: 8px; margin-bottom: 4px; }
  .contact__icon { width: 12px; height: 12px; flex: none; }
  .contact__web { font-weight: 600; color: var(--band-mid); }
  .card--back { display: flex; flex-direction: column; align-items: center; justify-content: center; }
  .card--back .brand-name { font-size: 52px; }
  .card--back .tagline { font-size: 18px; margin-top: 14px; letter-spacing: 3px; }
  .website-highlight {
    margin-top: 26px;
    padding: 7px 18px;
    font-size: 17px; font-weight: 600; letter-spacing: 0.5px;
    color: var(--on-band);
    background: linear-gradient(90deg, var(--band-deep), var(--band-light));
    border-radius: 3px;
  }
  .qr-space {
    position: absolute; right: 22px; bottom: 22px;
    width: 74px; height: 74px;
    border: 1.5px dashed var(--qr-line);
  }
</style>
</head>
<body>
<main class="sheet">
  <section class="card card--front" aria-label="Card front">
    <svg class="card__wave" viewBox="0 0 630 360" aria-hidden="true">
      <defs>
        <linearGradient id="bandGradient" x1="0" y1="0" x2="1" y2="0">
          <stop offset="0" stop-color="var(--band-deep)"/>
          <stop offset="0.5" stop-color="var(--band-mid)"/>
          <stop offset="1" stop-color="var(--band-light)"/>
        </linearGradient>
      </defs>
      <path d="M300,292 C390,326 490,340 630,336 L630,346 C480,350 380,334 300,292 Z" fill="var(--swoosh-grey)"/>
      <path d="M0,220 C120,212 210,250 300,292 C380,330 470,350 630,350 L630,360 L0,360 Z" fill="url(#bandGradient)"/>
    </svg>

    <div class="brand-block">
      <div class="brand-name">Bright Harbor</div>
      <div class="tagline">Cleaner &amp; Protectant</div>
    </div>

    <div class="person">
      <div class="person__name">Walt Ferris</div>
      <div class="person__role">Managing Director</div>
    </div>

    <div class="contact">
      <p class="contact__address">1200 Harbor Lane, Suite 4<br>Dune Bay</p>
      <ul class="contact__list">
        <li>
          <svg class="contact__icon" viewBox="0 0 12 12" aria-hidden="true"><path d="M2.5,1 L4.5,1 L5.2,3.6 L4,4.6 C4.6,6 5.8,7.3 7.4,8 L8.4,6.8 L11,7.5 L11,9.5 C11,10.3 10.3,11 9.5,11 C5,11 1,7 1,2.5 C1,1.7 1.7,1 2.5,1 Z" fill="var(--ink-soft)"/></svg>
          <span>555 014 2270</span>
        </li>
        <li>
          <svg class="contact__icon" viewBox="0 0 12 12" aria-hidden="true"><rect x="3" y="0.8" width="6" height="10.4" rx="1" fill="none" stroke="var(--ink-soft)" stroke-width="1.2"/><circle cx="6" cy="9.3" r="0.7" fill="var(--ink-soft)"/></svg>
          <span>555 014 2271</span>
        </li>
        <li>
          <svg class="contact__icon" viewBox="0 0 12 12" aria-hidden="true"><rect x="0.8" y="2.4" width="10.4" height="7.2" fill="none" stroke="var(--ink-soft)" stroke-width="1.2"/><path d="M0.8,2.6 L6,6.6 L11.2,2.6" fill="none" stroke="var(--ink-soft)" stroke-width="1.2"/></svg>
          <span>walt@brightharbor.example</span>
        </li>
        <li>
          <svg class="contact__icon" viewBox="0 0 12 12" aria-hidden="true"><circle cx="6" cy="6" r="5.2" fill="none" stroke="var(--band-mid)" stroke-width="1.1"/><ellipse cx="6" cy="6" rx="2.2" ry="5.2" fill="none" stroke="var(--band-mid)" stroke-width="1"/><path d="M0.8,6 L11.2,6" stroke="var(--band-mid)" stroke-width="1"/></svg>
          <span class="contact__web">www.brightharborwash.example</span>
        </li>
      </ul>
    </div>
  </section>

  <section class="card card--back" aria-label="Card back">
    <div class="brand-name">Bright Harbor</div>
    <div class="tagline">Cleaner &amp; Protectant</div>
    <div class="website-highlight">www.brightharborwash.example</div>
    <div class="qr-space" role="img" aria-label="Reserved space for QR code"></div>
  </section>
</main>
</body>
</html>
```